KRT Project Signage

Need a sign to be displayed in the front of properties currently under Construction or Renovation to advertise our company information. Need it to be Professional and Contemporary. We are a Design/Build Construction Company. Information should include Company Name, email, website, phone number. Attached: Logo and company brochure, also included and inspiration images

```html
<!DOCTYPE html>
<html lang="en">
<head>
<meta charset="utf-8">
<title>KRT Project Signage</title>
<link rel="stylesheet" href="https://fonts.googleapis.com/css2?family=Montserrat:wght@700;800&family=Poppins:wght@400;600;700&display=swap">
<style>
  :root {
    --page-bg: #b8b8b8;
    --ink: #0b0b0b;
    --accent: #f3ea44;
    --paper: #ffffff;
    --text-light: #ffffff;
  }
  * { margin: 0; padding: 0; box-sizing: border-box; }
  html, body {
    width: 686px;
    height: 1200px;
    overflow: hidden;
    background: var(--page-bg);
  }
  .sign {
    position: absolute;
    left: 23px;
    top: 120px;
    width: 640px;
    height: 960px;
    box-shadow: 0 10px 30px rgba(0,0,0,0.35);
  }
  .sign svg { display: block; width: 100%; height: 100%; }
  .name { font-family: "Montserrat", sans-serif; font-weight: 800; }
  .name-first { fill: var(--accent); }
  .name-last { fill: var(--text-light); }
  .role-text { font-family: "Poppins", sans-serif; font-weight: 600; fill: var(--ink); }
  .contact-text { font-family: "Poppins", sans-serif; font-weight: 400; fill: var(--text-light); }
  .phone-text { font-family: "Poppins", sans-serif; font-weight: 700; fill: var(--ink); }
  .company-text { font-family: "Poppins", sans-serif; font-weight: 600; fill: var(--ink); }
</style>
</head>
<body>
  <div class="sign">
    <svg viewBox="0 0 640 960" xmlns="http://www.w3.org/2000/svg">
      <defs>
        <linearGradient id="interiorTone" x1="0" y1="0" x2="0" y2="1">
          <stop offset="0" stop-color="#050505"/>
          <stop offset="0.45" stop-color="#1c1c1c"/>
          <stop offset="1" stop-color="#2e2e2e"/>
        </linearGradient>
      </defs>

      <rect class="interior-backdrop" x="0" y="0" width="640" height="800" fill="url(#interiorTone)" role="img" aria-label="Dark photograph of a modern furnished interior"/>

      <!-- name -->
      <text class="name name-first" x="119" y="129" font-size="100" textLength="391" lengthAdjust="spacingAndGlyphs">DANIEL</text>
      <text class="name name-last" x="144" y="218" font-size="100" textLength="332" lengthAdjust="spacingAndGlyphs">PARKER</text>

      <!-- role pill -->
      <rect x="58" y="251" width="510" height="39" rx="19.5" fill="var(--accent)"/>
      <text class="role-text" x="119" y="281" font-size="29" textLength="388" lengthAdjust="spacing">DESIGN &amp; BUILDER</text>

      <!-- location & mail icons -->
      <g class="icon-pin">
        <circle cx="287" cy="346" r="25" fill="var(--accent)"/>
        <path d="M287 331 a10 10 0 0 1 10 10 c0 8 -10 19 -10 19 s-10 -11 -10 -19 a10 10 0 0 1 10 -10z" fill="var(--ink)"/>
        <circle cx="287" cy="341" r="4" fill="var(--accent)"/>
      </g>
      <g class="icon-mail">
        <circle cx="352" cy="346" r="25" fill="var(--accent)"/>
        <rect x="337" y="336" width="30" height="20" fill="none" stroke="var(--ink)" stroke-width="2.5"/>
        <path d="M337 336 l15 12 l15 -12 M337 356 l11 -10 M367 356 l-11 -10" fill="none" stroke="var(--ink)" stroke-width="2.2"/>
      </g>

      <!-- address & email -->
      <text class="contact-text" x="320" y="422" text-anchor="middle" font-size="32">1450 NE 5th Ave., Ste. 310</text>
      <text class="contact-text" x="320" y="459" text-anchor="middle" font-size="32">Delray Beach, FL 33444</text>
      <text class="contact-text" x="313" y="514" text-anchor="middle" font-size="32">info@krtconstruction.com</text>

      <!-- yellow arc band -->
      <path d="M0 641 Q320 553 640 641 L640 788 L0 788 Z" fill="var(--accent)"/>

      <!-- phone & fax icons -->
      <g class="icon-phone">
        <circle cx="284" cy="601" r="27" fill="var(--ink)" stroke="var(--accent)" stroke-width="3"/>
        <path d="M274 590 c2 -2 5 -2 6 0 l3 5 c1 2 0 4 -2 5 c1 4 5 8 9 9 c1 -2 3 -3 5 -2 l5 3 c2 1 2 4 0 6 c-3 3 -7 4 -11 2 c-7 -3 -13 -9 -16 -16 c-2 -4 -1 -9 1 -12z" fill="var(--text-light)"/>
      </g>
      <g class="icon-fax">
        <circle cx="359" cy="601" r="27" fill="var(--ink)" stroke="var(--accent)" stroke-width="3"/>
        <rect x="345" y="595" width="7" height="18" rx="1.5" fill="var(--text-light)"/>
        <rect x="354" y="595" width="18" height="18" rx="1.5" fill="var(--text-light)"/>
        <rect x="357" y="587" width="12" height="9" fill="none" stroke="var(--text-light)" stroke-width="2"/>
        <path d="M357 600 h4 M363 600 h6 M357 604 h4 M363 604 h6 M357 608 h4 M363 608 h6" stroke="var(--ink)" stroke-width="2"/>
      </g>

      <!-- phone numbers -->
      <text class="phone-text" x="126" y="695" font-size="48" textLength="388" lengthAdjust="spacing">555-214-7730</text>
      <text class="phone-text" x="126" y="748" font-size="48" textLength="388" lengthAdjust="spacing">555.368.0942</text>

      <!-- company name block -->
      <rect x="0" y="787" width="640" height="173" fill="var(--paper)"/>
      <text class="company-text" x="315" y="868" text-anchor="middle" font-size="26" letter-spacing="2">KRT CONSTRUCTION</text>
    </svg>
  </div>
</body>
</html>
```